Elevating our current Business Card Design

We want to elevate our current business card with a new design to look like a zenith 300 company. We are a premium lubricant distributor (oil and grease).
We need 2 versions, version 1 is as per the uploaded a copy of our current business card with the English version.
For our Chinese version we need to use the front to be English in English and have the back of the card designed exactly like the front for all info to be in Chinese.
The design template needs to be such that we can amend the template with adding different information for each person's card.
The background colour of the card can be changed- we just need to clearly see all information on the card and logos.
The QJR and Ember steady logos cannot have any colour or display changes- only use the logos attached.
All logos need to be included and all information from the attached current card

```html
<!DOCTYPE html>
<html lang="en">
<head>
<meta charset="utf-8">
<title>Halvorn Business Card</title>
<link rel="stylesheet" href="https://fonts.googleapis.com/css2?family=Open+Sans:wght@400;600;700;800&display=swap">
<style>
  :root {
    --stage: #232324;
    --card: #1e1e21;
    --red: #e8261f;
    --red-dark: #b01a17;
    --gold: #e2a62a;
    --white: #ffffff;
    --grey: #c9c9cc;
    --badge: #f07a1c;
  }
  * { box-sizing: border-box; margin: 0; padding: 0; }
  html, body { width: 1200px; height: 780px; overflow: hidden; }
  body {
    background: var(--stage);
    font-family: "Open Sans", Arial, sans-serif;
    color: var(--white);
    position: relative;
  }
  .card {
    position: absolute;
    top: 225px;
    width: 540px;
    height: 330px;
    background: var(--card);
    border-radius: 4px;
    overflow: hidden;
  }
  .card--contact { left: 40px; }
  .card--brand { left: 620px; }

  /* partner names */
  .partners {
    display: flex;
    align-items: center;
    gap: 14px;
  }
  .card--contact .partners {
    position: absolute;
    left: 26px; top: 138px;
  }
  .partners__item {
    font-weight: 700;
    font-size: 15px;
    color: var(--white);
    white-space: nowrap;
  }
  .partners__sep {
    width: 1px; height: 20px;
    background: var(--grey);
  }

  .divider {
    position: absolute;
    left: 262px; top: 38px;
    width: 1px; height: 200px;
    background: linear-gradient(var(--card), var(--grey) 50%, var(--card));
  }

  .contact { position: absolute; left: 288px; top: 30px; }
  .contact__name { color: var(--red); font-size: 27px; font-weight: 700; line-height: 1.1; }
  .contact__role { font-size: 13.5px; font-weight: 600; margin-bottom: 14px; }
  .contact__list { list-style: none; }
  .contact__item {
    display: flex; align-items: center; gap: 9px;
    font-size: 12.5px; line-height: 21px;
  }
  .contact__icon { width: 12px; height: 12px; flex: none; }

  .address-band {
    position: absolute;
    left: 0; top: 270px;
    width: 410px; height: 32px;
    background: linear-gradient(var(--red), var(--red-dark));
    display: flex; align-items: center;
    padding-left: 70px;
    font-size: 14.5px; font-weight: 600;
  }
  .band-mark {
    position: absolute; left: 418px; top: 270px;
    height: 32px; display: flex; align-items: center; gap: 5px;
    color: var(--red); font-weight: 700; font-size: 14px;
  }
  .band-mark__dot { width: 9px; height: 9px; border-radius: 50%; background: var(--gold); }
  .gold-tab {
    position: absolute; right: 0; top: 270px;
    width: 30px; height: 32px; background: var(--gold);
  }

  /* brand side */
  .brand-mark {
    position: absolute; left: 0; right: 0; top: 78px;
    display: flex; justify-content: center; align-items: center; gap: 14px;
  }
  .brand-mark__dot { width: 26px; height: 26px; border-radius: 50%; background: var(--gold); }
  .brand-mark__name { color: var(--red); font-weight: 800; font-size: 66px; letter-spacing: 1px; }

  .credentials {
    position: absolute; left: 22px; right: 22px; bottom: 28px;
    display: flex; align-items: center; justify-content: space-between;
  }
  .membership { color: var(--white); font-weight: 700; font-size: 13px; white-space: nowrap; }
  .cert-badge { width: 36px; height: 36px; border-radius: 50%; background: var(--badge); flex: none; }
  .credentials .partners__item { font-size: 14px; }
</style>
</head>
<body>

<section class="card card--contact" aria-label="Contact side">
  <div class="partners">
    <span class="partners__item">HALVORN</span>
    <span class="partners__sep"></span>
    <span class="partners__item">TAVERO</span>
  </div>

  <div class="divider"></div>

  <div class="contact">
    <h1 class="contact__name">Mara Delacroix</h1>
    <p class="contact__role">Administration Executive</p>
    <ul class="contact__list">
      <li class="contact__item">
        <svg class="contact__icon" viewBox="0 0 12 12"><path d="M2 1l2.5 0 1 3-1.5 1a6 6 0 0 0 3 3l1-1.5 3 1v2.5a1 1 0 0 1-1 1A10 10 0 0 1 1 2a1 1 0 0 1 1-1z" fill="#e8261f"/></svg>
        1300 000 111
      </li>
      <li class="contact__item">
        <svg class="contact__icon" viewBox="0 0 12 12"><rect x="3" y="0.5" width="6" height="11" rx="1" fill="none" stroke="#e8261f" stroke-width="1.2"/><circle cx="6" cy="9.6" r=".7" fill="#e8261f"/></svg>
        +61 400 555 019
      </li>
      <li class="contact__item">
        <svg class="contact__icon" viewBox="0 0 12 12"><rect x="1" y="4" width="10" height="7" rx="1" fill="#e8261f"/><rect x="3" y="1" width="6" height="4" fill="none" stroke="#e8261f"/></svg>
        +61 8 5550 1234
      </li>
      <li class="contact__item">
        <svg class="contact__icon" viewBox="0 0 12 12"><circle cx="6" cy="6" r="5" fill="none" stroke="#e8261f" stroke-width="1.2"/><path d="M1 6h10M6 1c-2.5 3-2.5 7 0 10M6 1c2.5 3 2.5 7 0 10" fill="none" stroke="#e8261f"/></svg>
        www.halvorndirect.com
      </li>
      <li class="contact__item">
        <svg class="contact__icon" viewBox="0 0 12 12"><rect x="0.5" y="2" width="11" height="8" rx="1" fill="#e8261f"/><path d="M1 2.5l5 4 5-4" fill="none" stroke="#1e1e21"/></svg>
        mara.d@halvorndirect.com
      </li>
    </ul>
  </div>

  <div class="address-band">48 Freight Lane Carrow, WA 6199</div>
  <div class="band-mark"><span class="band-mark__dot"></span>HALVORN</div>
  <div class="gold-tab"></div>
</section>

<section class="card card--brand" aria-label="Brand side">
  <div class="brand-mark">
    <span class="brand-mark__dot"></span>
    <span class="brand-mark__name">HALVORN</span>
  </div>

  <div class="credentials">
    <span class="membership">Ember steady</span>
    <span class="cert-badge" role="img" aria-label="QJR certification badge"></span>
    <div class="partners">
      <span class="partners__item">HALVORN</span>
      <span class="partners__sep"></span>
      <span class="partners__item">TAVERO</span>
    </div>
    <span class="cert-badge" role="img" aria-label="QJR certification badge"></span>
    <span class="cert-badge" role="img" aria-label="QJR certification badge"></span>
  </div>
</section>

</body>
</html>
```